New Modern High end Gin Design

We are looking for a new design for our current gin. The gin is named Lamp Heron Gin. We are looking for the bottle to be blue and the lettering to be gold. Please add the design on the bottle. the picture of the current bottle is in the uploaded files. we will not be using the same bottle. See photo attached with bottle type we would like to use. We would also like to make the lamp heron imaged embossed

Font styles to use
Decorative

Colors
0054AA
0677BA
7BADD7
CADEEF
E8F1F8
0094D4
00A9DD
6FCCEA
C7EBF8
E9F6FB
FFC000
F8CF3A
FAE287
FDF2CF
FEFAEE

Requirements
Must have
• blue bottle
Nice to have
• ridges in the bottle

```html
<!DOCTYPE html>
<html lang="en">
<head>
<meta charset="utf-8">
<title>Lamp Heron Gin – Label</title>
<link rel="stylesheet" href="https://fonts.googleapis.com/css2?family=Rye&family=Bitter:wght@700&display=swap">
<style>
  :root {
    --ground: #267CBF;
    --gold-light: #F8E08A;
    --gold-mid: #E6C96A;
    --gold-deep: #B8962E;
    --gold-text: #F1D479;
  }
  html, body {
    margin: 0;
    padding: 0;
    width: 1200px;
    height: 1000px;
    overflow: hidden;
    background: var(--ground);
  }
  .label {
    display: block;
    width: 1200px;
    height: 1000px;
  }
  .brand-name {
    font-family: "Rye", serif;
    font-size: 84px;
    fill: url(#goldSheen);
  }
  .brand-type {
    font-family: "Rye", serif;
    font-size: 96px;
    fill: url(#goldSheen);
  }
  .tagline {
    font-family: "Bitter", serif;
    font-weight: 700;
    font-size: 11px;
    letter-spacing: 3.5px;
    fill: var(--gold-text);
  }
  .side-note {
    font-family: "Bitter", serif;
    font-weight: 700;
    font-size: 22px;
    letter-spacing: 2px;
    fill: var(--gold-text);
  }
  .distiller {
    font-family: "Bitter", serif;
    font-weight: 700;
    font-size: 29px;
    fill: url(#goldSheen);
  }
  .bottled-by {
    font-family: "Bitter", serif;
    font-weight: 700;
    font-size: 11px;
    letter-spacing: 2.5px;
    fill: var(--gold-text);
  }
  .measure {
    font-family: "Bitter", serif;
    font-weight: 700;
    font-size: 20px;
    fill: var(--gold-text);
  }
  .measure-unit { font-size: 10px; }
  .rule { fill: none; stroke: url(#goldSheen); }
  .fine-rule { fill: none; stroke: var(--gold-mid); stroke-width: 1.2; }
  .ornament-zone { fill: var(--gold-mid); opacity: 0.08; }
</style>
</head>
<body>
<svg class="label" viewBox="0 0 1200 1000" xmlns="http://www.w3.org/2000/svg">
  <defs>
    <linearGradient id="goldSheen" x1="0" y1="0" x2="1" y2="1">
      <stop offset="0" stop-color="#FBE9A0"/>
      <stop offset="0.55" stop-color="#E8CB6C"/>
      <stop offset="1" stop-color="#B8962E"/>
    </linearGradient>
    <radialGradient id="sceneTone" cx="0.5" cy="0.45" r="0.6">
      <stop offset="0" stop-color="#E8CB6C" stop-opacity="0.55"/>
      <stop offset="1" stop-color="#C9A53C" stop-opacity="0.3"/>
    </radialGradient>
    <path id="crestLine" d="M 400 313 A 340 340 0 0 1 800 313"/>
    <path id="nameArc" d="M 361 470 A 292 292 0 0 1 839 470"/>
    <path id="bottledArc" d="M 490 580 A 110 110 0 0 0 710 580"/>
    <path id="distillerWave" d="M 345 628 C 440 650 505 737 600 737 C 700 737 770 650 860 610"/>
  </defs>

  <!-- flourish areas beside the side notes -->
  <g role="img" aria-label="Gold engraved scroll flourishes framing the label">
    <rect class="ornament-zone" x="338" y="445" width="55" height="145" rx="26"/>
    <rect class="ornament-zone" x="807" y="445" width="55" height="145" rx="26"/>
  </g>

  <!-- top crest -->
  <text class="tagline"><textPath href="#crestLine" startOffset="50%" text-anchor="middle">CAREFULLY CRAFTED</textPath></text>
  <path class="fine-rule" d="M 323 374 A 342 342 0 0 1 877 374"/>
  <path class="rule" stroke-width="4" d="M 330 387 A 334 334 0 0 1 870 387"/>

  <!-- brand name -->
  <text class="brand-name"><textPath href="#nameArc" startOffset="50%" text-anchor="middle" textLength="520" lengthAdjust="spacingAndGlyphs">LAMP HERON</textPath></text>
  <path class="rule" stroke-width="4" d="M 411 434 A 298 298 0 0 1 789 434"/>
  <text class="brand-type" x="600" y="448" text-anchor="middle" textLength="171" lengthAdjust="spacingAndGlyphs">GIN</text>

  <!-- side notes -->
  <text class="side-note" x="445" y="522" text-anchor="middle">SMALL</text>
  <text class="side-note" x="445" y="546" text-anchor="middle">BATCH</text>
  <text class="side-note" x="750" y="522" text-anchor="middle">GLEN</text>
  <text class="side-note" x="750" y="546" text-anchor="middle">ASHBY</text>

  <!-- medallion -->
  <circle cx="597" cy="563" r="96" class="fine-rule" stroke-width="1.5"/>
  <circle cx="597" cy="563" r="90" fill="none" stroke="url(#goldSheen)" stroke-width="4"/>
  <circle cx="597" cy="563" r="82" fill="url(#sceneTone)" role="img" aria-label="Engraved scene of two workers pumping a handcar along a railway track"/>

  <text class="bottled-by"><textPath href="#bottledArc" startOffset="50%" text-anchor="middle">BOTTLED &amp; DISTILLED BY</textPath></text>

  <!-- bottom waves -->
  <path fill="url(#goldSheen)" d="M 343 601 C 450 598 525 690 597 702 C 675 690 750 598 863 601 C 752 604 680 696 597 706 C 520 696 448 606 343 605 Z"/>
  <path fill="url(#goldSheen)" d="M 343 650 C 420 655 480 700 530 744 C 476 706 416 662 343 654 Z"/>
  <path fill="url(#goldSheen)" d="M 857 650 C 780 655 720 700 672 744 C 726 706 786 662 857 654 Z"/>

  <text class="distiller"><textPath href="#distillerWave" startOffset="50%" text-anchor="middle" textLength="540" lengthAdjust="spacing">COPPER KETTLE DISTILLERY</textPath></text>

  <!-- measures -->
  <text class="measure" x="400" y="724" text-anchor="middle"><tspan class="measure-unit">VOL </tspan>40%</text>
  <text class="measure" x="786" y="724" text-anchor="middle">750<tspan class="measure-unit">ML</tspan></text>
</svg>
</body>
</html>
```